Refresh of far from plain IT company website

Our web site is starting to show it's age. You can see the existing site here: www.plumbwick.net. As a growing company we want to come across as a dynamic collection of IT experts.

We want to update the design so are open to any colour palette and look, but want to retain our current table logo. We use the logo on our business cards but with a white background - see the attached file, so you don't need to keep the brown or the green.

The design should consider the range of browsers that will be looking at the site - so please show how it will look on a wide screen laptop and a 768x1024 tablet.

We want to add some pages about our team and their skills, probably with photos of each person on the team.

This is an uncoded project - the PSD files of the design is required, not coding.
Updates

Thanks everyone for the submissions so far.  It's a holiday day in the UK today but we will get some feedback on the designs so far out to you.

Target Market(s)

Architects and other creative types looking for IT support

Industry/Entity Type

Business

Font styles to use
Serif
Sans Serif

Requirements
Must have
• Must look good on a laptop and an iPad.

```html
<!DOCTYPE html>
<html lang="en">
<head>
<meta charset="utf-8">
<title>plumbwick — IT support</title>
<link href="https://fonts.googleapis.com/css2?family=Open+Sans:ital,wght@0,400;0,600;0,700;1,400&display=swap" rel="stylesheet">
<style>
:root{
  --plum:#8c1a4b;
  --gold:#c9990b;
  --ink:#333;
  --muted:#7a7a7a;
  --icon:#bab5b5;
  --band:#efeeee;
  --footer:#4f4f4f;
  --base:#1f1f1f;
  --hero:#5a5a5a;
  --clientbox:#4a4a4a;
}
*{margin:0;padding:0;box-sizing:border-box}
html,body{width:759px;height:1200px;overflow:hidden;background:#fff}
body{position:relative;font-family:'Open Sans',sans-serif;color:var(--ink)}
.abs{position:absolute}
.topline{left:0;top:0;width:759px;height:5px;background:#4a4a4a}
.header{left:0;top:5px;width:759px;height:58px;background:#fff}
.brand{left:88px;top:18px;display:flex;align-items:center;gap:8px;font-size:19px;font-weight:700;color:var(--plum)}
.brand i{display:block;width:13px;height:13px;background:var(--gold)}
.nav{right:85px;top:0;height:58px;display:flex;font-size:10.4px}
.nav a{color:var(--plum);text-decoration:none;padding:0 7.5px;line-height:64px}
.nav a.active{background:#f2f2f2;color:#222;padding:0 9px}
.hero{left:0;top:63px;width:759px;height:265px;background:radial-gradient(ellipse at 48% 40%,#6e6a5e 0%,#5c5c5c 35%,#3e3e3e 100%)}
.hero h1{position:absolute;left:101px;top:172px;font-weight:400;font-size:21.6px;line-height:28px;color:#fff}
.arrow{top:115px;width:16px;height:34px;background:#2e2e2e;color:#ccc;font-size:14px;line-height:34px;text-align:center}
.dots{left:359px;top:313px;display:flex;gap:2px}
.dots span{width:7px;height:7px;border-radius:50%;background:#d6d6d6}
.dots span.on{background:var(--plum)}
.h2{font-weight:400;font-size:18px;color:var(--plum)}
.card{top:398px;width:137px;height:164px;border:1px solid #e3e3e3;text-align:center}
.card svg{margin-top:11px}
.card .label{position:absolute;left:-1px;right:-1px;top:91px;height:14px;background:var(--gold);color:#fff;font-size:9px;line-height:14px}
.card p{position:absolute;left:6px;right:6px;top:112px;font-size:7px;line-height:13px;color:var(--muted)}
.about{left:86px;width:580px;font-size:7.2px;line-height:13px;color:var(--muted)}
.band{left:0;top:726px;width:759px;height:359px;background:var(--band)}
.more{font-size:7.5px;font-style:italic;color:var(--muted)}
.thumb{left:87px;width:81px;height:81px}
.post{left:178px;width:181px}
.post h3,.quote h3{font-size:8.6px;font-weight:400;color:#333;margin-bottom:3px}
.post p,.quote p{font-size:7.2px;line-height:13px;color:var(--muted);text-align:justify}
.post time{display:block;margin-top:5px;font-size:7px;font-style:italic;color:var(--muted)}
.clientlogo{left:389px;width:88px;height:35px;background:var(--clientbox);color:#fff;font-size:9.5px;font-weight:700;display:flex;align-items:center;justify-content:center}
.quote{left:487px;width:182px}
.footer{left:0;top:1085px;width:759px;height:91px;background:var(--footer);color:#fff}
.footer h4{position:absolute;left:87px;top:19px;font-size:11.5px;font-weight:600}
.session{position:absolute;left:87px;top:50px;width:95px;height:19px;background:#fff;border:1px solid #ccc;font-size:6.5px;color:#999;padding-left:6px;line-height:17px}
.go{position:absolute;left:186px;top:50px;width:22px;height:19px;background:var(--plum);border:1px solid #fff;font-size:8.5px;font-weight:700;line-height:17px;text-align:center}
.fnav{position:absolute;right:85px;display:flex;gap:15px;font-size:10.2px}
.base{left:0;top:1176px;width:759px;height:24px;background:var(--base)}
.social{position:absolute;left:85px;top:3px;display:flex;gap:2.5px}
.social span{width:18px;height:18px;border-radius:50%;background:#5e5e5e}
.copy{position:absolute;right:85px;top:6px;font-size:7px;color:#eee}
</style>
</head>
<body>
<div class="abs topline"></div>
<header class="abs header">
  <div class="abs brand"><i></i>plumbwick</div>
  <nav class="abs nav">
    <a class="active">Home</a><a>About us</a><a>What we do</a><a>News blog</a><a>Articles</a><a>Clients</a><a>Partners</a>
  </nav>
</header>

<section class="abs hero" role="img" aria-label="Chalkboard with drawn hanging light bulbs, one glowing yellow, and a hand holding chalk">
  <h1>Serious IT Support<br>For Business</h1>
</section>
<div class="abs arrow" style="left:0">&#10216;</div>
<div class="abs arrow" style="right:0">&#10217;</div>
<div class="abs dots"><span></span><span></span><span class="on"></span><span></span><span></span></div>

<h2 class="abs h2" style="left:84px;top:360px">What We Do ??</h2>

<div class="abs card" style="left:83px">
  <svg width="62" height="62" viewBox="0 0 62 62"><circle cx="31" cy="31" r="31" fill="var(--icon)"/><circle cx="31" cy="27" r="10" fill="#fff"/><rect x="26" y="36" width="10" height="6" fill="#fff"/><rect x="27" y="43" width="8" height="2" fill="#fff"/></svg>
  <div class="label">IT Support &amp; Management</div>
  <p>Lorem Ipsum is simply dummy text of the printing and typesetting industry. Lorem Ipsum is simply dummy ...</p>
</div>
<div class="abs card" style="left:234px">
  <svg width="62" height="62" viewBox="0 0 62 62"><circle cx="31" cy="31" r="31" fill="var(--icon)"/><path d="M19 38a7 7 0 0 1 1-14 10 10 0 0 1 19-3 8 8 0 0 1 4 17z" fill="#fff"/><path d="M26 44l10-10m0 0h-6m6 0v6" stroke="var(--icon)" stroke-width="3" fill="none"/></svg>
  <div class="label">Cloud Computing</div>
  <p>Lorem Ipsum is simply dummy text of the printing and typesetting industry. Lorem Ipsum is simply dummy ...</p>
</div>
<div class="abs card" style="left:386px">
  <svg width="62" height="62" viewBox="0 0 62 62"><circle cx="31" cy="31" r="31" fill="var(--icon)"/><ellipse cx="28" cy="20" rx="11" ry="4" fill="#fff"/><rect x="17" y="24" width="22" height="6" rx="3" fill="#fff"/><rect x="17" y="32" width="22" height="6" rx="3" fill="#fff"/><rect x="17" y="40" width="18" height="5" rx="2.5" fill="#fff"/><path d="M42 34v14M35 41h14" stroke="#fff" stroke-width="4"/></svg>
  <div class="label">Disaster Recovery</div>
  <p>Lorem Ipsum is simply dummy text of the printing and typesetting industry. Lorem Ipsum is simply dummy ...</p>
</div>
<div class="abs card" style="left:538px">
  <svg width="62" height="62" viewBox="0 0 62 62"><circle cx="31" cy="31" r="31" fill="var(--icon)"/><rect x="17" y="17" width="28" height="28" fill="none" stroke="#fff" stroke-width="2"/><path d="M21 42l8-20 8 20M24 35h10" stroke="#fff" stroke-width="3" fill="none"/></svg>
  <div class="label">CAD Services</div>
  <p>Lorem Ipsum is simply dummy text of the printing and typesetting industry. Lorem Ipsum is simply dummy ...</p>
</div>

<h2 class="abs h2" style="left:86px;top:589px">The Plumbwick Difference</h2>
<div class="abs about" style="top:621px">Plumbwick was established with a specific aim: to consistently deliver an advanced and comprehensive IT service for ambitious growing companies across many industry sectors. We aim to provide the very best in service and support, and to aid business growth through the effective and skilled use of modern IT solutions.</div>
<div class="abs about" style="top:651px">Founded in 2003, we have grown rapidly and have delivered successful business solutions to small and medium sized businesses, working with customers across a wide IT spectrum. The knowledge, experience and expertise which we have gained managing systems and networks for a range of companies over many years enables us to develop with confidence, the best IT solution for our clients.</div>

<div class="abs band"></div>
<h2 class="abs h2" style="left:86px;top:741px">News Blog</h2>
<span class="abs more" style="left:321px;top:752px">View More</span>
<h2 class="abs h2" style="left:410px;top:745px">Clients</h2>
<span class="abs more" style="left:631px;top:756px">View More</span>

<div class="abs thumb" style="top:789px;background:linear-gradient(135deg,#1d5fa8,#5fc4ee 60%,#163a6e)" role="img" aria-label="Photo of a businessman in front of a blue digital interface"></div>
<article class="abs post" style="top:786px"><h3>Lorem ipsum dolor</h3><p>adipiscing elit. Etiam quis placerat urna. Nulla nu adipiscing non ornardfe non, commodo non ipsum dolor sit. adipiscing elit. Etiam quis placerat urna. Nulla nu adipiscing....</p><time>17/04/14</time></article>

<div class="abs thumb" style="top:886px;background:linear-gradient(135deg,#f4f6f8,#c9d2dc 60%,#8f9aa6)" role="img" aria-label="Photo of hands typing on a keyboard"></div>
<article class="abs post" style="top:883px"><h3>Lorem ipsum dolor</h3><p>adipiscing elit. Etiam quis placerat urna. Nulla nu adipiscing non ornardfe non, commodo non ipsum dolor sit. adipiscing elit. Etiam quis placerat urna. Nulla nu adipiscing....</p><time>06/04/14</time></article>

<div class="abs thumb" style="top:986px;background:linear-gradient(135deg,#f5f3ef,#d8cfc2 60%,#a89580)" role="img" aria-label="Photo of a man drawing a chart on glass"></div>
<article class="abs post" style="top:983px"><h3>Lorem ipsum dolor</h3><p>adipiscing elit. Etiam quis placerat urna. Nulla nu adipiscing non ornardfe non, commodo non ipsum dolor sit. adipiscing elit. Etiam quis placerat urna. Nulla nu adipiscing....</p><time>28/03/14</time></article>

<div class="abs clientlogo" style="top:794px">Hollis Crane Avery</div>
<article class="abs quote" style="top:792px"><h3>Lorem ipsum</h3><p>“adipiscing elit. Etiam quis placerat urna. Nulla nu adipiscing non ornardfe non, commodo non ipsum dolor sit. adipiscing elit. Etiam quis placerat urna. Nulla nu adipiscing.... ”</p></article>

<div class="abs clientlogo" style="top:893px">Marlow Pike</div>
<article class="abs quote" style="top:890px"><h3>Lorem ipsum</h3><p>“adipiscing elit. Etiam quis placerat urna. Nulla nu adipiscing non ornardfe non, commodo non ipsum dolor sit. adipiscing elit. Etiam quis placerat urna. Nulla nu adipiscing.... ”</p></article>

<div class="abs clientlogo" style="top:990px">QT Studio</div>
<article class="abs quote" style="top:987px"><h3>Lorem ipsum</h3><p>“adipiscing elit. Etiam quis placerat urna. Nulla nu adipiscing non ornardfe non, commodo non ipsum dolor sit. adipiscing elit. Etiam quis placerat urna. Nulla nu adipiscing.... ”</p></article>

<footer class="abs footer">
  <h4>Remote</h4>
  <div class="session">Enter Session Id</div>
  <div class="go">GO</div>
  <nav class="fnav" style="top:19px"><span>Home</span><span>About us</span><span>What we do</span><span>News blog</span><span>Articles</span><span>Clients</span><span>Partners</span></nav>
  <nav class="fnav" style="top:49px;gap:24px"><span>Contact</span><span>Support</span><span>Terms</span></nav>
</footer>
<div class="abs base">
  <div class="social"><span></span><span></span><span></span><span></span><span></span></div>
  <div class="copy">© 2014 All rights reserved</div>
</div>
</body>
</html>
```